BrellomarUSA /The Daxolite & Daxolite X

Bringing to market a revolutionay new products. UVC sanitizing machines have been used by hospitals for years in operating rooms to kill viruses and bacteria. The problem is those machines cost anywhere for $65,000 to $125,000 each machine making the proven very effective technology unavailable to most industires that need them We have made 2 models that use the exact same effective technolgy that are very affordable. Our main product is The Daxolite. Tis machine is a mobile 216w unit that can effectively treat up to 1500sq ft and kill 99.9% of viruses (Covid and bacteria in 30 minutes. This unit can be used in areas such as schools, churches, nursing homes, daycares, resturaunts, casinos(especially casino bathrooms). offices, public transport, planes, vacational Rentals, etc.
Our smaller compact but powerful unit The Daxolite X is compact and powerful and can treat areas up to 864 sq ft. this unit is for use in hotel rooms, cruise ship cabins, Ambulances, School buses, and other small areas.
We all have been seeing people using sprayers spraying unknown and untested chemicals all over surfaces. there has been no long term testing and all I can picture is kids touching these surfaces and putting their fingers in their mouths. In years this will be the asbestos, roundup and talcum powder in the near future.
These machines eliminate the risk of those chemicals. Are completly safe and have been used by major medical facilities for years.
I am looking for a website to promote and sell these 2 products. We need to market to all the prospective types of clients that could use these and show their own customers how they have responsibly took action in tried and true technology to protect them.
The main company for these products is BrellomarUSA. We are also going to be selling this side of the business as a service business where we are looking for partners around the U.S to join our team to be able to provide UVC cleaning to clients that would rather call a professionla service to come out and sanitize their location rathe than having staff do this on their own.
Looking for the basics of a website design with a simple page where they can purchase the machines. We currently have a facebook page contest that is near end with great designs. I will attach those or links in the coming days. I need this all done, setup and hosted with the ability to have constant updates. I no absolutely know anything about coding. I can add on a constant basis wording, descriptions etc. whatever is needed.
I will upload more pictures daily.
Update- Here is some boi info for site.
About The Daxolite.
UV germicidal is limited to a single wavelength of UV-C at 253.7nm. The Daxolite 360 technology is a 216w system built to produce the very effective range with an extensive range of germicidal UVC. This extended range delivers a germicidal intensity that penetrates the cell walls of microorganisms and causes irreparable damage. That’s what makes our high Intensity mobile UVC Daxolite Machine so extremely fast and effective at reducing microbial loads like the Covid Virus.

Large Medical facilities have been using this same technology in operating rooms for years but at a cost of $65k-$125k

We have taken that same technolgy and built a system that any business or School system can use the same proven and effective technology at a price they can afford.

Why The Daxolite?

Manual cleaning leaves on average 47% of surface areas untouched. The Daxolite ensures those areas are sanitized.
No more of spraying harmful or long term untested chemicals need to be sprayed. Much like the Asbestos, roundup and talcum powders of the past.
An extremely fast and effective addition to your cleaning & sanitzing schedule.

Time Matters!

Every second counts when you feel your school or business may have a possible issue. Roll out The Daxolite and start killing it immediately. No need to wait for staff, chemicals or delays. Set up in just minutes. Clear the area and turn it on. The Daxolite gets to work immediatley.

About US .

BrellomarUSA/The Daxolite was founded in early 2020 as the emmergence of Covid-19 began. CEO/Owner- Dale Porvick with a over 16 yrs. in the LED lighting field has used his experience in lighting to create a reasonable priced product and service to help the everyday school or business. With years of being around and involved with all types of lighting including Germicidal lamps in Hospital settings
he created the very expensive alternative that can be used by thousands of industries to help and slow down this deadly Virus.

"Our Motto" Any technology that is available to assist should not be limited by price.

Target Market(s)

Schools both public and private, hotels, Vacation rentals, daycares, nursing homes, casinos, cruise lines

Coding

Number of Pages Required

4 page

```html
<!DOCTYPE html>
<html lang="en">
<head>
<meta charset="utf-8">
<title>BrellomarUSA – The Daxolite homepage concepts</title>
<link rel="stylesheet" href="https://fonts.googleapis.com/css2?family=Montserrat:wght@600;700;800&family=Open+Sans:wght@400;600&display=swap">
<style>
:root{
  --navy:#0f2a6b;
  --navy-deep:#0b1d4d;
  --footer:#0d1a3e;
  --red:#d9142a;
  --red-dark:#b30f21;
  --ink:#2b2f3a;
  --muted:#6b7183;
  --line:#dfe3ea;
  --board:#e9eaec;
  --white:#ffffff;
  --photo-cool-a:#c9d6e8;
  --photo-cool-b:#7f97bd;
  --photo-room-a:#b9b4aa;
  --photo-room-b:#6e747c;
}
*{box-sizing:border-box;margin:0;padding:0}
html,body{width:876px;height:1200px;overflow:hidden;background:var(--board)}
body{position:relative;font-family:"Open Sans",Arial,sans-serif;color:var(--ink)}
.page{position:absolute;top:23px;width:388px;height:1160px;background:var(--white);box-shadow:0 2px 8px rgba(0,0,0,.18);overflow:hidden;display:flex;flex-direction:column}
.page--classic{left:35px}
.page--angled{left:453px}
h1,h2,h3,h4{font-family:"Montserrat",Arial,sans-serif}
.btn{display:inline-block;font-family:"Montserrat",Arial,sans-serif;font-weight:700;font-size:5px;letter-spacing:.3px;text-transform:uppercase;color:var(--white);background:var(--red);padding:4px 9px;border-radius:2px}
.btn--navy{background:var(--navy)}
.photo{display:block}

/* nav */
.site-nav{height:35px;display:flex;align-items:center;padding:0 16px;gap:12px;background:var(--white);border-bottom:1px solid var(--line)}
.brand{display:flex;align-items:center;gap:4px;font-family:"Montserrat",Arial,sans-serif;font-weight:800;font-size:8px;color:var(--navy)}
.brand__dot{width:9px;height:9px;border-radius:50%;background:var(--red)}
.site-nav__links{display:flex;gap:9px;margin-left:auto;font-size:4.6px;font-weight:600;color:var(--ink)}
.site-nav__phone{font-size:4.6px;font-weight:600;color:var(--red)}

/* hero */
.hero{height:160px;position:relative;overflow:hidden}
.hero__photo{position:absolute;inset:0}
.page--classic .hero__photo{background:linear-gradient(100deg,#f1f4f9 0%,#e2e9f3 45%,var(--photo-cool-a) 70%,var(--photo-cool-b) 100%)}
.page--angled .hero{background:var(--navy)}
.page--angled .hero__photo{left:45%;background:linear-gradient(120deg,var(--photo-cool-a),var(--photo-cool-b));clip-path:polygon(22% 0,100% 0,100% 100%,0 100%)}
.hero__stripe{position:absolute;left:0;bottom:0;width:100%;height:14px;background:var(--red);clip-path:polygon(0 100%,100% 0,100% 100%)}
.hero__content{position:relative;padding:36px 0 0 22px;width:200px}
.hero__title{font-size:13px;line-height:1.15;font-weight:800;color:var(--navy)}
.page--angled .hero__title{color:var(--white)}
.hero__text{font-size:4.8px;line-height:1.5;margin:6px 0 8px;color:var(--muted)}
.page--angled .hero__text{color:#c9d3ea}

/* why */
.why{height:118px;padding:14px 22px 0;text-align:center}
.section-title{font-size:9.5px;font-weight:800;color:var(--navy)}
.section-title::after{content:"";display:block;width:18px;height:2px;background:var(--red);margin:4px auto 0}
.why__grid{display:flex;gap:20px;margin-top:14px}
.why__item{flex:1}
.why__icon{width:16px;height:16px;margin:0 auto 6px;display:block}
.why__text{font-size:4.5px;line-height:1.5;color:var(--muted)}

/* about product */
.about{height:255px;display:flex;align-items:center;padding:0 22px;gap:16px;position:relative}
.page--angled .about{background:linear-gradient(180deg,#fff 0%,#f4f6fa 100%)}
.about__visual{position:relative;width:150px;height:200px;flex:none}
.about__circle{position:absolute;left:8px;top:38px;width:118px;height:118px;border-radius:50%;background:var(--red)}
.about__machine{position:absolute;left:46px;top:10px;width:62px;height:182px;border-radius:4px;background:linear-gradient(180deg,#f2f4f7 0%,#c7ccd4 60%,#9aa1ad 100%)}
.about__copy{flex:1}
.about__title{font-size:10px;font-weight:800;color:var(--navy);margin-bottom:6px}
.about__text{font-size:4.6px;line-height:1.6;color:var(--muted);margin-bottom:9px}

/* time matters */
.time{height:175px;display:flex;position:relative;overflow:hidden}
.time__photo{width:50%;background:linear-gradient(160deg,var(--photo-room-a),var(--photo-room-b))}
.time__panel{width:50%;background:var(--navy);color:var(--white);padding:34px 20px 0}
.page--angled .time{background:var(--navy)}
.page--angled .time__photo{position:absolute;left:0;top:0;height:100%;width:55%;clip-path:polygon(0 0,100% 0,78% 100%,0 100%)}
.page--angled .time__panel{margin-left:auto;background:transparent}
.panel-title{font-size:10.5px;font-weight:800;margin-bottom:6px}
.panel-text{font-size:4.6px;line-height:1.6;margin-bottom:9px;color:#d6ddee}

/* about us */
.about-us{height:175px;display:flex;position:relative;overflow:hidden}
.about-us__panel{width:50%;background:var(--red);color:var(--white);padding:34px 20px 0}
.about-us__panel .panel-text{color:#ffe1e4}
.about-us__photo{width:50%;background:linear-gradient(200deg,#d7d9dd,var(--photo-room-b))}
.page--angled .about-us{background:var(--red)}
.page--angled .about-us__panel{background:transparent}
.page--angled .about-us__photo{position:absolute;right:0;top:0;height:100%;width:55%;clip-path:polygon(22% 0,100% 0,100% 100%,0 100%)}

/* testimonials */
.clients{height:124px;padding:14px 22px 0;text-align:center}
.clients__grid{display:flex;gap:14px;margin-top:12px}
.client{flex:1;display:flex;gap:6px;text-align:left;align-items:flex-start}
.client__avatar{width:20px;height:20px;border-radius:50%;flex:none;background:linear-gradient(150deg,#c9b8a6,#7d6f63);border:1.5px solid var(--red)}
.client__name{font-family:"Montserrat",Arial,sans-serif;font-size:5px;font-weight:700;color:var(--navy);margin-bottom:2px}
.client__quote{font-size:4.4px;line-height:1.5;color:var(--muted)}

/* footer */
.site-footer{height:118px;background:var(--footer);color:var(--white);padding:18px 22px 0;position:relative;overflow:hidden}
.page--angled .site-footer::before{content:"";position:absolute;left:0;top:0;width:100%;height:16px;background:var(--white);clip-path:polygon(0 0,100% 0,0 100%)}
.page--angled .site-footer::after{content:"";position:absolute;right:0;top:0;width:120px;height:100%;background:var(--navy-deep);clip-path:polygon(40% 0,100% 0,100% 100%,0 100%);z-index:0}
.footer__cols{display:flex;gap:16px;position:relative;z-index:1}
.footer__col h4{font-size:5.5px;font-weight:700;margin-bottom:6px}
.footer__col h4::after{content:"";display:block;width:10px;height:1.5px;background:var(--red);margin-top:3px}
.footer__col li{list-style:none;font-size:4.4px;line-height:1.9;color:#b9c2da}
.footer__col--brand{width:78px}
.footer__col--news{margin-left:auto;width:110px}
.newsletter{display:flex;margin-top:2px}
.newsletter__input{flex:1;height:12px;background:var(--white);font-size:4.4px;color:var(--muted);padding:3px 4px}
.newsletter__btn{height:12px;background:var(--red);font-size:4.4px;font-weight:700;padding:3px 6px}
.footer__legal{position:absolute;left:0;right:0;bottom:0;height:16px;border-top:1px solid rgba(255,255,255,.12);font-size:4.2px;color:#8f9abb;text-align:center;line-height:16px;z-index:1}
.brand--light{color:var(--white)}
</style>
</head>
<body>

<!-- Concept A: straight sections -->
<main class="page page--classic">
  <header class="site-nav">
    <div class="brand"><span class="brand__dot"></span>BrellomarUSA</div>
    <nav class="site-nav__links"><span>Home</span><span>About Us</span><span>Products</span><span>Services</span><span>Partners</span><span>Contact</span></nav>
  </header>

  <section class="hero">
    <div class="hero__photo photo" role="img" aria-label="UVC sanitizing machine glowing blue in a bright clinical room"></div>
    <div class="hero__content">
      <h1 class="hero__title">We Build Custom Packaging UVC sanitizing machines</h1>
      <p class="hero__text">Hospital-grade UVC disinfection built for schools, hotels and businesses at a fair price.</p>
      <span class="btn">Request quote</span>
    </div>
  </section>

  <section class="why">
    <h2 class="section-title">Why The Daxolite?</h2>
    <div class="why__grid">
      <div class="why__item">
        <svg class="why__icon" viewBox="0 0 16 16"><circle cx="8" cy="8" r="7" fill="none" stroke="#d9142a" stroke-width="1.2"/><path d="M4.5 8.2l2.3 2.3 4.7-4.8" fill="none" stroke="#0f2a6b" stroke-width="1.3"/></svg>
        <p class="why__text">Manual cleaning leaves 47% of surfaces untouched. The Daxolite reaches those areas.</p>
      </div>
      <div class="why__item">
        <svg class="why__icon" viewBox="0 0 16 16"><circle cx="8" cy="8" r="7" fill="none" stroke="#d9142a" stroke-width="1.2"/><path d="M5 5l6 6M11 5l-6 6" stroke="#0f2a6b" stroke-width="1.3"/></svg>
        <p class="why__text">No more spraying untested chemicals across desks, doors and shared surfaces.</p>
      </div>
      <div class="why__item">
        <svg class="why__icon" viewBox="0 0 16 16"><circle cx="8" cy="8" r="7" fill="none" stroke="#d9142a" stroke-width="1.2"/><path d="M8 4v4.5l3 1.8" fill="none" stroke="#0f2a6b" stroke-width="1.3"/></svg>
        <p class="why__text">A fast, effective addition to your cleaning and sanitizing schedule.</p>
      </div>
    </div>
  </section>

  <section class="about">
    <div class="about__visual">
      <div class="about__circle"></div>
      <div class="about__machine photo" role="img" aria-label="The Daxolite mobile UVC sanitizing unit"></div>
    </div>
    <div class="about__copy">
      <h2 class="about__title">About The Daxolite</h2>
      <p class="about__text">The Daxolite 360 is a 216w system producing an extended range of germicidal UVC. It penetrates the cell walls of microorganisms and causes irreparable damage, reducing microbial loads fast. Hospitals pay $65k to $125k for this technology; we built it at a price any school or business can afford.</p>
      <span class="btn">Learn more</span>
    </div>
  </section>

  <section class="time">
    <div class="time__photo photo" role="img" aria-label="Office room being sanitized by a UVC unit"></div>
    <div class="time__panel">
      <h2 class="panel-title">Time Matters!</h2>
      <p class="panel-text">Every second counts. Roll out The Daxolite, clear the area and turn it on. Set up in minutes with no staff, chemicals or delays.</p>
      <span class="btn">Get started</span>
    </div>
  </section>

  <section class="about-us">
    <div class="about-us__panel">
      <h2 class="panel-title">About Us</h2>
      <p class="panel-text">Founded in early 2020, BrellomarUSA brings over 16 years of LED lighting experience to an affordable germicidal product and service for everyday schools and businesses.</p>
      <span class="btn btn--navy">Read more</span>
    </div>
    <div class="about-us__photo photo" role="img" aria-label="UVC unit standing in a hallway with tiled floor"></div>
  </section>

  <section class="clients">
    <h2 class="section-title">What Our clients say?</h2>
    <div class="clients__grid">
      <div class="client"><div class="client__avatar" role="img" aria-label="Client portrait"></div><div><p class="client__name">Maria Talvest</p><p class="client__quote">Easy to roll out and our rooms feel safer every single day.</p></div></div>
      <div class="client"><div class="client__avatar" role="img" aria-label="Client portrait"></div><div><p class="client__name">Jon Ordell</p><p class="client__quote">Setup took minutes and our staff no longer spray chemicals daily.</p></div></div>
      <div class="client"><div class="client__avatar" role="img" aria-label="Client portrait"></div><div><p class="client__name">Kira Banes</p><p class="client__quote">Parents trust our classrooms more since we added this machine.</p></div></div>
    </div>
  </section>

  <footer class="site-footer">
    <div class="footer__cols">
      <div class="footer__col footer__col--brand"><div class="brand brand--light"><span class="brand__dot"></span>BrellomarUSA</div></div>
      <div class="footer__col"><h4>Navigation</h4><ul><li>Home</li><li>About Us</li><li>Products</li><li>Services</li><li>Contact</li></ul></div>
      <div class="footer__col"><h4>Links</h4><ul><li>Partners</li><li>Shop</li><li>FAQ</li><li>Support</li></ul></div>
      <div class="footer__col footer__col--news"><h4>Subscribe to newsletter</h4><div class="newsletter"><span class="newsletter__input">Your email</span><span class="newsletter__btn">Send</span></div></div>
    </div>
    <p class="footer__legal">© 2021 BrellomarUSA. All rights reserved.</p>
  </footer>
</main>

<!-- Concept B: angled sections -->
<main class="page page--angled">
  <header class="site-nav">
    <div class="brand"><span class="brand__dot"></span>BrellomarUSA</div>
    <nav class="site-nav__links"><span>Home</span><span>About Us</span><span>Products</span><span>Services</span><span>Partners</span><span>Contact</span></nav>
  </header>

  <section class="hero">
    <div class="hero__photo photo" role="img" aria-label="UVC sanitizing machine glowing blue in a clinical room"></div>
    <div class="hero__stripe"></div>
    <div class="hero__content">
      <h1 class="hero__title">We Build Custom Packaging UVC sanitizing machines</h1>
      <p class="hero__text">Hospital-grade UVC disinfection built for schools, hotels and businesses at a fair price.</p>
      <span class="btn">Request quote</span>
    </div>
  </section>

  <section class="why">
    <h2 class="section-title">Why The Daxolite?</h2>
    <div class="why__grid">
      <div class="why__item">
        <svg class="why__icon" viewBox="0 0 16 16"><circle cx="8" cy="8" r="7" fill="none" stroke="#d9142a" stroke-width="1.2"/><path d="M4.5 8.2l2.3 2.3 4.7-4.8" fill="none" stroke="#0f2a6b" stroke-width="1.3"/></svg>
        <p class="why__text">Manual cleaning leaves 47% of surfaces untouched. The Daxolite reaches those areas.</p>
      </div>
      <div class="why__item">
        <svg class="why__icon" viewBox="0 0 16 16"><circle cx="8" cy="8" r="7" fill="none" stroke="#d9142a" stroke-width="1.2"/><path d="M5 5l6 6M11 5l-6 6" stroke="#0f2a6b" stroke-width="1.3"/></svg>
        <p class="why__text">No more spraying untested chemicals across desks, doors and shared surfaces.</p>
      </div>
      <div class="why__item">
        <svg class="why__icon" viewBox="0 0 16 16"><circle cx="8" cy="8" r="7" fill="none" stroke="#d9142a" stroke-width="1.2"/><path d="M8 4v4.5l3 1.8" fill="none" stroke="#0f2a6b" stroke-width="1.3"/></svg>
        <p class="why__text">A fast, effective addition to your cleaning and sanitizing schedule.</p>
      </div>
    </div>
  </section>

  <section class="about">
    <div class="about__visual">
      <div class="about__circle"></div>
      <div class="about__machine photo" role="img" aria-label="The Daxolite mobile UVC sanitizing unit"></div>
    </div>
    <div class="about__copy">
      <h2 class="about__title">About The Daxolite</h2>
      <p class="about__text">The Daxolite 360 is a 216w system producing an extended range of germicidal UVC. It penetrates the cell walls of microorganisms and causes irreparable damage, reducing microbial loads fast. Hospitals pay $65k to $125k for this technology; we built it at a price any school or business can afford.</p>
      <span class="btn">Learn more</span>
    </div>
  </section>

  <section class="time">
    <div class="time__photo photo" role="img" aria-label="Office room being sanitized by a UVC unit"></div>
    <div class="time__panel">
      <h2 class="panel-title">Time Matters!</h2>
      <p class="panel-text">Every second counts. Roll out The Daxolite, clear the area and turn it on. Set up in minutes with no staff, chemicals or delays.</p>
      <span class="btn">Get started</span>
    </div>
  </section>

  <section class="about-us">
    <div class="about-us__panel">
      <h2 class="panel-title">About Us</h2>
      <p class="panel-text">Founded in early 2020, BrellomarUSA brings over 16 years of LED lighting experience to an affordable germicidal product and service for everyday schools and businesses.</p>
      <span class="btn btn--navy">Read more</span>
    </div>
    <div class="about-us__photo photo" role="img" aria-label="UVC unit standing in a hallway with tiled floor"></div>
  </section>

  <section class="clients">
    <h2 class="section-title">What Our clients say?</h2>
    <div class="clients__grid">
      <div class="client"><div class="client__avatar" role="img" aria-label="Client portrait"></div><div><p class="client__name">Maria Talvest</p><p class="client__quote">Easy to roll out and our rooms feel safer every single day.</p></div></div>
      <div class="client"><div class="client__avatar" role="img" aria-label="Client portrait"></div><div><p class="client__name">Jon Ordell</p><p class="client__quote">Setup took minutes and our staff no longer spray chemicals daily.</p></div></div>
      <div class="client"><div class="client__avatar" role="img" aria-label="Client portrait"></div><div><p class="client__name">Kira Banes</p><p class="client__quote">Parents trust our classrooms more since we added this machine.</p></div></div>
    </div>
  </section>

  <footer class="site-footer">
    <div class="footer__cols">
      <div class="footer__col footer__col--brand"><div class="brand brand--light"><span class="brand__dot"></span>BrellomarUSA</div></div>
      <div class="footer__col"><h4>Navigation</h4><ul><li>Home</li><li>About Us</li><li>Products</li><li>Services</li><li>Contact</li></ul></div>
      <div class="footer__col"><h4>Links</h4><ul><li>Partners</li><li>Shop</li><li>FAQ</li><li>Support</li></ul></div>
      <div class="footer__col footer__col--news"><h4>Subscribe to newsletter</h4><div class="newsletter"><span class="newsletter__input">Your email</span><span class="newsletter__btn">Send</span></div></div>
    </div>
    <p class="footer__legal">© 2021 BrellomarUSA. All rights reserved.</p>
  </footer>
</main>

</body>
</html>
```